CREATE A BUSINESS CARD FOR A BOAT CLEANING SERVICE

WE ARE STARTING A NEW BOAT CLEANING BUSINESS. WE DIVE UNDERWATER TO CLEAN BOAT HULLS, JETTIES, UNDERWATER STRUCTURES ETC. WE ARE LOOKING FOR AN UPPERMARKET MODERN LOGO AND BUSINESS CARD AS ALOT OF OUR TARGET MARKET WILL BE HIGH END. YOU HAVE TO DESIGN A BUSINESS CARD AND LOGO SEPERATELY .
THE BUSINESS CARD DIMESNION MUST BE STANDARD SIZE.
The standard dimensions of a printed business card are 3.5 x 2 inches

Target Market(s)

UNDERWATER SERVICED

Industry/Entity Type

Business

Contact Information for Business Card

HOLLAND UNDERWATER SERVICES

Font styles to use
Serif

Colors

Designer to choose colors to be used in the design.

Requirements
Must have
• HOLLAND
Nice to have
• dark
Should not have
• more than 3 colors

```html
<!DOCTYPE html>
<html lang="en">
<head>
<meta charset="utf-8">
<title>Holland Underwater Service – Business Card</title>
<link href="https://fonts.googleapis.com/css2?family=Josefin+Sans:wght@300;400&family=Work+Sans:wght@400;500&display=swap" rel="stylesheet">
<style>
  :root {
    --backdrop: #3b3330;
    --card: #151617;
    --card-edge: #232527;
    --silver: #8e9194;
    --blue: #2f7fc4;
    --white: #f2f2f2;
    --muted: #5d6064;
  }
  * { box-sizing: border-box; margin: 0; padding: 0; }
  html, body { width: 1200px; height: 715px; overflow: hidden; }
  body {
    background: var(--backdrop);
    font-family: "Work Sans", sans-serif;
    position: relative;
  }
  .card {
    position: absolute;
    top: 203px;
    width: 540px;
    height: 309px;
    background: var(--card);
    border: 1px solid var(--card-edge);
    border-radius: 3px;
    box-shadow: 0 14px 30px rgba(0,0,0,.45);
  }
  .card--front { left: 45px; }
  .card--back { left: 615px; }

  .wordmark {
    position: absolute;
    text-align: center;
    font-family: "Josefin Sans", sans-serif;
    font-weight: 300;
  }
  .wordmark__name {
    display: block;
    font-size: 34px;
    letter-spacing: 18px;
    padding-left: 18px;
  }
  .wordmark__tagline {
    display: block;
    font-size: 15px;
    letter-spacing: 5px;
    padding-left: 5px;
    margin-top: 6px;
  }
  .card--front .wordmark {
    left: 0; right: 0; top: 118px;
    color: var(--silver);
  }
  .card--back .wordmark {
    left: 22px; width: 250px; top: 120px;
    color: var(--blue);
  }
  .card--back .wordmark__name { font-size: 25px; letter-spacing: 13px; padding-left: 13px; }
  .card--back .wordmark__tagline { font-size: 11px; letter-spacing: 3.5px; padding-left: 3.5px; }

  .divider {
    position: absolute;
    left: 290px; top: 70px;
    width: 1px; height: 150px;
    background: var(--muted);
  }
  .contact {
    position: absolute;
    left: 308px; top: 68px;
    color: var(--white);
    font-size: 12.5px;
    line-height: 19px;
  }
  .contact__name {
    color: var(--blue);
    font-size: 21px;
    font-weight: 500;
    letter-spacing: .5px;
    line-height: 24px;
  }
  .contact__role { font-size: 12.5px; margin-bottom: 4px; }
  .contact__line { display: flex; align-items: center; gap: 6px; }
  .contact__line svg { width: 9px; height: 9px; flex: none; fill: var(--muted); }
  .contact__line--plain { padding-left: 15px; }

  .badges {
    position: absolute;
    left: 296px; top: 240px;
    display: flex; align-items: center; gap: 34px;
  }
  .badges__partner {
    width: 50px; height: 38px;
    border-radius: 50%;
    background: #1f6b86;
  }
  .badges__brand {
    color: var(--white);
    font-family: "Josefin Sans", sans-serif;
    font-weight: 400;
    font-size: 24px;
    letter-spacing: 1px;
  }
</style>
</head>
<body>
  <section class="card card--front" aria-label="Card front">
    <div class="wordmark">
      <span class="wordmark__name">HOLLAND</span>
      <span class="wordmark__tagline">UNDERWATER SERVICE</span>
    </div>
  </section>

  <section class="card card--back" aria-label="Card back">
    <div class="wordmark">
      <span class="wordmark__name">HOLLAND</span>
      <span class="wordmark__tagline">UNDERWATER SERVICE</span>
    </div>
    <div class="divider"></div>
    <div class="contact">
      <p class="contact__name">MARTIN CALLOWAY</p>
      <p class="contact__role">President</p>
      <p class="contact__line contact__line--plain">410, 318- 9th Ave. NW</p>
      <p class="contact__line contact__line--plain">Calgary, AB T2N 1K4</p>
      <p class="contact__line">
        <svg viewBox="0 0 10 10"><path d="M2 0.5 L3.8 2.6 L2.9 3.6 Q4 6 6.4 7.1 L7.4 6.2 L9.5 8 L8.2 9.5 Q1 8.5 0.5 1.8 Z"/></svg>
        (403) 555-0192
      </p>
      <p class="contact__line">
        <svg viewBox="0 0 10 10"><path d="M0.5 2 H9.5 V8 H0.5 Z M1.2 2.6 L5 5.4 L8.8 2.6" fill="none" stroke="#5d6064" stroke-width="1"/></svg>
        info@hollandunderwater.com
      </p>
      <p class="contact__line">
        <svg viewBox="0 0 10 10"><circle cx="5" cy="5" r="4.3" fill="none" stroke="#5d6064" stroke-width="1"/><path d="M0.7 5 H9.3 M5 0.7 Q2.5 5 5 9.3 M5 0.7 Q7.5 5 5 9.3" fill="none" stroke="#5d6064" stroke-width=".8"/></svg>
        www.hollandunderwater.com
      </p>
    </div>
    <div class="badges">
      <div class="badges__partner" role="img" aria-label="Partner badge"></div>
      <span class="badges__brand">HOLLAND</span>
    </div>
  </section>
</body>
</html>
```